Business Cards for a law firm

Business cards for our law firm. Use our silhoette logo and OAK PARTNERS - check our website (www.oakpartners.example)

Contact Information for Business Card

our silhouette logo, OAK PARTNERS, 800-555-0147, Dorian Pemberton, dorian@oakpartners.example

Requirements
Must have
• our silhouette logo, OAK PARTNERS, 800-555-0147, Dorian Pemberton, dorian@oakpartners.example

```html
<!DOCTYPE html>
<html lang="en">
<head>
<meta charset="utf-8">
<title>Oak Partners — Business Cards</title>
<link href="https://fonts.googleapis.com/css2?family=Cinzel:wght@500;600;700&display=swap" rel="stylesheet">
<style>
  :root {
    --page-bg: #d3d4d6;
    --card-deep: #1f2c5f;
    --card-light: #273a7a;
    --ink: #ffffff;
  }
  * { margin: 0; padding: 0; box-sizing: border-box; }
  html, body {
    width: 900px; height: 1200px; overflow: hidden;
    background: var(--page-bg);
  }
  .canvas { position: relative; width: 900px; height: 1200px; }
  .card {
    position: absolute; left: 134px; width: 632px; height: 364px;
    background: linear-gradient(135deg, var(--card-deep) 0%, var(--card-light) 100%);
    color: var(--ink);
    font-family: "Cinzel", serif;
  }
  .card--front { top: 210px; }
  .card--back { top: 624px; }
  .logo-mark {
    position: absolute; left: 59px; width: 66px; height: 66px;
    background: var(--ink);
  }
  .card--front .logo-mark { top: 148px; }
  .card--back .logo-mark { top: 111px; }
  .wordmark {
    position: absolute; left: 142px;
    white-space: nowrap;
    font-weight: 700; font-size: 52px; letter-spacing: 0.5px;
    line-height: 1;
  }
  .card--front .wordmark { top: 160px; }
  .card--back .wordmark { top: 123px; }
  .front-url {
    position: absolute; left: 0; right: 0; top: 317px;
    text-align: center; font-size: 11px; font-weight: 700;
    letter-spacing: 4px;
  }
  .holder {
    position: absolute; right: 340px; top: 250px; text-align: right;
  }
  .holder-name { font-size: 18px; font-weight: 700; letter-spacing: 1px; line-height: 1; }
  .holder-role { font-size: 14px; font-weight: 500; letter-spacing: 1px; margin-top: 10px; line-height: 1; }
  .divider {
    position: absolute; left: 316px; top: 237px; width: 2px; height: 72px;
    background: var(--ink);
  }
  .contacts { position: absolute; left: 337px; top: 234px; list-style: none; }
  .contact {
    display: flex; align-items: center; gap: 5px;
    height: 27px; font-size: 11px; font-weight: 600; letter-spacing: 0.5px;
    white-space: nowrap;
  }
  .contact--phone { font-size: 14px; letter-spacing: 2.5px; }
  .contact svg { width: 14px; height: 14px; flex: none; fill: var(--ink); }
</style>
</head>
<body>
<main class="canvas">
  <section class="card card--front">
    <div class="logo-mark" role="img" aria-label="Firm silhouette logo"></div>
    <h1 class="wordmark">OAK PARTNERS</h1>
    <p class="front-url">WWW.OAKPARTNERS.EXAMPLE</p>
  </section>

  <section class="card card--back">
    <div class="logo-mark" role="img" aria-label="Firm silhouette logo"></div>
    <h2 class="wordmark">OAK PARTNERS</h2>
    <div class="holder">
      <p class="holder-name">DORIAN PEMBERTON</p>
      <p class="holder-role">ATTORNEY</p>
    </div>
    <div class="divider"></div>
    <ul class="contacts">
      <li class="contact contact--phone">
        <svg viewBox="0 0 24 24" aria-hidden="true"><path d="M6.6 10.8a15.1 15.1 0 0 0 6.6 6.6l2.2-2.2c.3-.3.7-.4 1-.2 1.1.4 2.3.6 3.6.6.6 0 1 .4 1 1V20c0 .6-.4 1-1 1A17 17 0 0 1 3 4c0-.6.4-1 1-1h3.5c.6 0 1 .4 1 1 0 1.3.2 2.5.6 3.6.1.3 0 .7-.2 1z"/></svg>
        800-555-0147
      </li>
      <li class="contact">
        <svg viewBox="0 0 24 24" aria-hidden="true"><path d="M2 5h20v14H2z" fill="var(--ink)"/><path d="M3 6l9 7 9-7" stroke="#213064" stroke-width="1.6" fill="none"/></svg>
        DORIAN@OAKPARTNERS.EXAMPLE
      </li>
      <li class="contact">
        <svg viewBox="0 0 24 24" aria-hidden="true"><g fill="none" stroke="var(--ink)" stroke-width="1.8"><circle cx="12" cy="12" r="9"/><ellipse cx="12" cy="12" rx="4" ry="9"/><path d="M3 12h18M5 7h14M5 17h14"/></g></svg>
        WWW.OAKPARTNERS.EXAMPLE
      </li>
    </ul>
  </section>
</main>
</body>
</html>
```